New Business Card Design Project LORVANTI-Italy

we are LORVANTI-Italy
our company in the market for 3 years we are luxury cosmetic company and its about time for a facelift :)
i will like to have elegant luxurious and unique business card
that will give the person that get it a unique, luxurious and elegant impression
I'm VERY OPEN FOR NEW IDEAS , even duo i add a few files of things that i see on line and i like them

i add my logo as well
my website is LORVANTI.COM
(if you would like to see the main style that we have)

Target Market(s)

adult that have money :)

Industry/Entity Type

Business

Contact Information for Business Card

Name - Dario Lorvanti
Position - CEO and CO Founder
address - 4817 E Halvern
telephone - 555-384-1926
email - dario@lorvanti.com
fax - 555-384-1926
website - LORVANTI.COM

Colors
000000
959595
fbee3e
ffffff

Requirements
Must have
• big logo in GOLD color
• elegant look
• impressive
Nice to have
• not must but maybe classy pattern background
• not must but maybe emblem
• maybe clear plastic business card
Should not have
• colors
• images

```html
<!DOCTYPE html>
<html lang="en">
<head>
<meta charset="utf-8">
<title>LORVANTI-Italy Business Card</title>
<link rel="stylesheet" href="https://fonts.googleapis.com/css2?family=EB+Garamond:wght@400;500;600&display=swap">
<style>
  :root {
    --stage: #1c1c1c;
    --card: #0d0d0d;
    --card-edge: #262626;
    --gold: #d9a93a;
    --white: #f4f4f4;
  }
  * { margin: 0; padding: 0; box-sizing: border-box; }
  html, body {
    width: 1200px;
    height: 833px;
    overflow: hidden;
    background: var(--stage);
  }
  .stage {
    position: relative;
    width: 1200px;
    height: 833px;
    display: flex;
    align-items: center;
    justify-content: center;
    gap: 40px;
  }
  .card {
    width: 520px;
    height: 298px;
    background: var(--card);
    border: 1px solid var(--card-edge);
    border-radius: 3px;
    font-family: "EB Garamond", Georgia, serif;
    display: flex;
    flex-direction: column;
    align-items: center;
    justify-content: center;
    text-align: center;
  }

  /* Front */
  .brand-mark {
    width: 86px;
    height: 86px;
    border: 3px solid var(--gold);
    border-radius: 50%;
    margin-bottom: 18px;
  }
  .brand-name {
    color: var(--gold);
    font-size: 52px;
    font-weight: 500;
    letter-spacing: 2px;
    line-height: 1;
  }

  /* Back */
  .card-back { padding-top: 10px; }
  .holder-name {
    color: var(--gold);
    font-size: 30px;
    font-weight: 600;
    line-height: 1.1;
  }
  .holder-role {
    color: var(--white);
    font-size: 16px;
    margin-top: 2px;
  }
  .divider {
    width: 42px;
    height: 1px;
    background: var(--gold);
    margin: 12px 0 10px;
  }
  .contact {
    color: var(--white);
    font-size: 15px;
    line-height: 1.45;
  }
  .contact .label { color: var(--gold); margin-right: 3px; }
  .contact .item + .item { margin-left: 10px; }
</style>
</head>
<body>
  <main class="stage">
    <section class="card card-front" aria-label="Card front">
      <div class="brand-mark" aria-hidden="true"></div>
      <div class="brand-name">LORVANTI</div>
    </section>

    <section class="card card-back" aria-label="Card back">
      <div class="holder-name">Dario Lorvanti</div>
      <div class="holder-role">CEO and CO Founder</div>
      <div class="divider"></div>
      <div class="contact">
        <div class="address">LORVANTI-Italy 4817 E Halvern</div>
        <div class="lines">
          <span class="item"><span class="label">P:</span>555-384-1926</span>
          <span class="item"><span class="label">F:</span>555-384-1926</span>
          <span class="item"><span class="label">E:</span>dario@lorvanti.com</span>
        </div>
        <div class="website">LORVANTI.COM</div>
      </div>
    </section>
  </main>
</body>
</html>
```